Corvane Holdings , new business card design

investment firm with corporate clients . need double sided business card , vertical and horizontal options ,logo must be clear. prefer pantone colors only and sharp design. website also www.corvane.ae

Khalid Bin Tarrafi
Managing Director
Tel. +971 4 387 2940
Mobile +971 50 518 2403
khalid@corvane.ae
Q-Span Plaza, officw 18-B07, Warqa Gardens, Dubai

Contact Information for Business Card

Khalid Bin Tarrafi
Managing Director

Font styles to use
Serif

Colors

Designer to choose colors to be used in the design.

```html
<!DOCTYPE html>
<html lang="en">
<head>
<meta charset="utf-8">
<title>Corvane Holdings – Business Card</title>
<link href="https://fonts.googleapis.com/css2?family=Jost:wght@300;400;500&display=swap" rel="stylesheet">
<style>
  :root {
    --stage: #2a2a2c;
    --card-dark: #0c0d12;
    --card-light: #ffffff;
    --brand-blue: #3d6b99;
    --ink: #1e2530;
    --ink-soft: #3a404a;
    --white: #ffffff;
  }
  * { box-sizing: border-box; margin: 0; padding: 0; }
  html, body {
    width: 1200px; height: 852px; overflow: hidden;
    background: var(--stage);
    font-family: "Jost", "Helvetica Neue", Arial, sans-serif;
  }
  .stage {
    position: relative; width: 1200px; height: 852px;
    display: flex; flex-direction: column; align-items: center; justify-content: center;
    gap: 40px;
  }
  .card {
    position: relative; width: 620px; height: 354px;
    border-radius: 18px; overflow: hidden;
  }
  .card--back { background: var(--card-dark); display: flex; align-items: center; justify-content: center; }
  .card--front { background: var(--card-light); }

  .wordmark {
    font-weight: 300; text-transform: uppercase; line-height: 1;
    display: flex; align-items: center; gap: 14px; white-space: nowrap;
  }
  .wordmark__mark { width: 12px; height: 12px; background: var(--brand-blue); flex: none; }
  .card--back .wordmark { color: var(--white); font-size: 34px; letter-spacing: 8px; }
  .card--front .wordmark {
    position: absolute; left: 34px; top: 172px;
    color: var(--ink); font-size: 21px; letter-spacing: 4px;
  }

  .divider {
    position: absolute; left: 352px; top: 92px; width: 1.5px; height: 190px;
    background: var(--brand-blue);
  }
  .contact { position: absolute; left: 380px; top: 84px; color: var(--ink-soft); }
  .contact__name {
    color: var(--brand-blue); font-weight: 400; font-size: 17px;
    text-transform: uppercase; letter-spacing: 0.2px;
  }
  .contact__role { font-size: 14px; font-weight: 400; margin-top: 1px; }
  .contact__address { font-size: 14px; line-height: 1.3; margin-top: 22px; }
  .contact__list { list-style: none; margin-top: 16px; font-size: 14px; line-height: 1.45; }
  .contact__list li { display: flex; align-items: center; gap: 9px; }
  .contact__list svg { width: 10px; height: 10px; flex: none; fill: var(--brand-blue); }
</style>
</head>
<body>
<main class="stage">
  <section class="card card--back" aria-label="Card back">
    <div class="wordmark"><span class="wordmark__mark"></span>Corvane Holdings</div>
  </section>

  <section class="card card--front" aria-label="Card front">
    <div class="wordmark"><span class="wordmark__mark"></span>Corvane Holdings</div>
    <div class="divider"></div>
    <div class="contact">
      <p class="contact__name">Khalid Bin Tarrafi</p>
      <p class="contact__role">Managing Director</p>
      <p class="contact__address">Q-Span Plaza, officw 18-B07,<br>Warqa Gardens, Dubai</p>
      <ul class="contact__list">
        <li>
          <svg viewBox="0 0 10 10" aria-hidden="true"><path d="M2 0.5 L3.6 2.6 L2.7 3.6 Q3.6 5.6 6.4 7.3 L7.4 6.4 L9.5 8 L8.3 9.5 Q4.5 9.2 1.8 6 Q0.4 3.8 0.6 1.7 Z"/></svg>
          +971 4 387 2940
        </li>
        <li>
          <svg viewBox="0 0 10 10" aria-hidden="true"><path d="M2.5 0 H7.5 Q8 0 8 0.5 V9.5 Q8 10 7.5 10 H2.5 Q2 10 2 9.5 V0.5 Q2 0 2.5 0 Z M3 1 V8 H7 V1 Z"/></svg>
          +971 50 518 2403
        </li>
        <li>
          <svg viewBox="0 0 10 10" aria-hidden="true"><path d="M0 2 H10 V8.5 H0 Z M1 3 V7.5 H9 V3 L5 5.8 Z M1.6 3 L5 5.2 L8.4 3 Z"/></svg>
          khalid@corvane.ae
        </li>
      </ul>
    </div>
  </section>
</main>
</body>
</html>
```